Meridale Nutrition needs Stationary and a business card

We would like to use our current logo. The text can be moved around as needed. The stationary needs to be a 'first page' where the logo is more prominent to be impressive on higher quality paper and a second page where the logo is more subtle where there will be much more information on the page. There are 2 clinic locations which will need include name, address, phone number, fax number, web address. The business card should be single sided and contain this information also.
The design must be contemporary and sophisticated as this is a science based diet run out of a medical clinic.

Target Market(s)

People wanting to lose weight, athletes looking to optimise performance, people with arthritis or fighting cancer

Industry/Entity Type

Business

Contact Information for Business Card

must use the logo. I have attached an example card with the practice details on it. there must be space for the doctors name. Also the website www.meridalenutrition.com.au

Requirements
Must have
• the logo, the business adresses and phone numbers, the website, the doctors name and qualifications
Nice to have
• some creativity
Should not have
• Do not simply reproduce the existing card please

```html
<!DOCTYPE html>
<html lang="en">
<head>
<meta charset="utf-8">
<title>Meridale Nutrition — Stationery</title>
<link rel="stylesheet" href="https://fonts.googleapis.com/css2?family=Source+Sans+3:wght@400;600;700&display=swap">
<style>
  :root{
    --backdrop:#cbcbcb;
    --paper:#e7e7e7;
    --navy:#356899;
    --cyan:#1fc4f4;
    --ink:#3a3a3a;
    --grey:#5a5a5a;
    --white:#ffffff;
  }
  *{box-sizing:border-box;margin:0;padding:0}
  html,body{width:1200px;height:809px;overflow:hidden}
  body{background:var(--backdrop);font-family:"Source Sans 3",Arial,sans-serif;color:var(--ink);position:relative}

  .letterhead{position:absolute;left:54px;top:53px;width:496px;height:699px;background:var(--paper);box-shadow:1px 1px 3px rgba(0,0,0,.25)}
  .brand{position:absolute;text-align:center}
  .brand-mark{display:block;margin:0 auto;border-radius:50%;background:var(--cyan);border:3px solid var(--navy)}
  .brand-name{display:block;font-weight:700;color:var(--navy);letter-spacing:.2px;white-space:nowrap}

  .letterhead .brand{left:30px;top:33px;width:116px}
  .letterhead .brand-mark{width:60px;height:60px}
  .letterhead .brand-name{font-size:11px;margin-top:8px}

  .clinics{position:absolute;top:51px;left:250px;display:flex;font-size:9.6px;line-height:12.3px;color:var(--grey);white-space:nowrap}
  .clinic-a{text-align:right;padding-right:10px;border-right:1px solid #888;width:114px}
  .clinic-b{padding-left:11px}
  .clinic-name{color:var(--navy);font-weight:600}
  .tel{color:var(--navy);font-weight:600}

  .letter{position:absolute;left:36px;top:222px;width:436px;font-size:8.7px;line-height:10.8px;color:var(--ink)}
  .letter p{margin-bottom:10.8px}
  .letter .salutation{margin-bottom:22px}
  .signoff{position:absolute;left:36px;top:458px;font-size:8.8px;line-height:12px}
  .signature{position:absolute;left:114px;top:471px;width:72px;height:28px;background:linear-gradient(90deg,rgba(53,104,153,.18),rgba(53,104,153,.05));border-radius:3px}

  .band{position:absolute;left:0;bottom:0;width:100%;height:22px;display:flex;font-size:9.2px;color:var(--white);white-space:nowrap}
  .band-left{background:var(--navy);flex:0 0 50.5%;display:flex;align-items:center;padding-left:22px;overflow:hidden}
  .band-right{background:var(--cyan);flex:1;display:flex;align-items:center;justify-content:flex-end;padding-right:22px;overflow:hidden}
  .band strong{font-weight:700;margin-right:3px}
  .band-dot{position:absolute;top:-2px;width:26px;height:26px;border-radius:50%;background:var(--cyan);border:2px solid var(--white);left:calc(50.5% - 13px)}

  .envelope{position:absolute;left:568px;top:394px;width:584px;height:360px}
  .envelope-flap{position:absolute;left:0;top:0}
  .flap-dot{position:absolute;left:265px;top:21px;width:54px;height:54px;border-radius:50%;background:var(--cyan);border:3px solid var(--white)}
  .envelope-body{position:absolute;left:0;top:98px;width:584px;height:262px;background:var(--paper);box-shadow:1px 1px 3px rgba(0,0,0,.25)}
  .envelope .brand{left:14px;top:13px;width:120px}
  .envelope .brand-mark{width:60px;height:60px}
  .envelope .brand-name{font-size:11px;margin-top:8px}
  .envelope .band{height:24px;font-size:9px}
  .envelope .band-left{flex-basis:50.7%;padding-left:30px}
  .envelope .band-dot{left:calc(50.7% - 13px)}
  .envelope .band-right{padding-right:24px}
</style>
</head>
<body>

<section class="letterhead">
  <div class="brand">
    <span class="brand-mark"></span>
    <span class="brand-name">MERIDALE NUTRITION</span>
  </div>

  <div class="clinics">
    <div class="clinic-a">
      <div class="clinic-name">Harlow Park</div>
      <div>52-54 Ashgrove Road</div>
      <div>Harlow Park NSW 2190</div>
      <div><span class="tel">Tel:</span> 02 9100 4821</div>
    </div>
    <div class="clinic-b">
      <div class="clinic-name">Elmsbury</div>
      <div>118 Linwood Street</div>
      <div>Elmsbury NSW 2045</div>
      <div><span class="tel">Tel:</span> 02 9100 7364</div>
    </div>
  </div>

  <div class="letter">
    <p class="salutation">Dear Mr. Smith,</p>
    <p>Lorem ipsum dolor sit amet, consectetur adipiscing elit. Donec orci purus, luctus vitae dignissim eu, iaculis sed purus. Vivamus faucibus, ipsum nec aliquet viverra, leo mauris condimentum ligula, sit amet sagittis enim ligula quis arcu. Nam egestas tortor id nisi porttitor mattis. In tortor ante, ultricies in suscipit a, tempus non massa. Vivamus et auctor mi.</p>
    <p>Fusce vel massa nulla. Phasellus nec eros mauris, et scelerisque orci. Donec malesuada orci vitae nulla accumsan porta a id massa. Quisque accumsan iaculis magna sit amet fringilla. Maecenas consequat, magna eget tincidunt semper, odio nibh rutrum mi, id feugiat ante nisi eu risus. Vestibulum nunc orci, rhoncus a placerat in, ultricies in mi. Cras mattis varius eros, vel fringilla nisi suscipit eget.</p>
    <p>Quisque scelerisque sagittis nulla at porttitor. Mauris a justo et tellus interdum tristique. Sed id augue vitae urna euismod commodo aliquet a quam. Pellentesque arcu velit, cursus et malesuada ut, consequat et diam. Nullam erat sem, rhoncus id ullamcorper vitae, rhoncus et arcu. In ultricies ultricies nulla, ut rutrum nisi iaculis at. Donec eu magna a metus ornare faucibus.</p>
    <p>Fusce aliquet faucibus ultricies. Morbi semper, est id tincidunt gravida, sem arcu adipiscing lacus, ac bibendum nulla leo eu purus. Quisque nec diam sed risus consectetur a ccumsan quis quis nibh. Vestibulum id purus lorem.</p>
  </div>

  <div class="signoff">Daniel Rowe<br>Co-Founder &amp; CEO</div>
  <div class="signature" role="img" aria-label="Handwritten signature of Daniel Rowe"></div>

  <div class="band">
    <div class="band-left"><strong>Shoulder and Elbow :</strong> www.armjointclinic.com.au</div>
    <div class="band-right"><strong>Knee surgery :</strong> www.kneecarecentre.com.au</div>
    <span class="band-dot"></span>
  </div>
</section>

<section class="envelope">
  <svg class="envelope-flap" width="584" height="100" viewBox="0 0 584 100">
    <path d="M0 98 L12 36 Q20 0 56 0 L528 0 Q564 0 572 36 L584 98 Z" fill="#356899"/>
  </svg>
  <span class="flap-dot"></span>

  <div class="envelope-body">
    <div class="brand">
      <span class="brand-mark"></span>
      <span class="brand-name">MERIDALE NUTRITION</span>
    </div>
    <div class="band">
      <div class="band-left"><strong>Harlow Park :</strong> 52-54 Ashgrove Road, Harlow Park NSW 2190</div>
      <div class="band-right"><strong>Elmsbury :</strong> 118 Linwood Street, Elmsbury NSW 2045</div>
      <span class="band-dot"></span>
    </div>
  </div>
</section>

</body>
</html>
```